Business card design for new eCommerce site focusing on integrity and strong businsess tactics

We need a business card that will stand out and be memorable. Something with color that matches our company logo colors. Think high end version of Pactivo. There are 2 logos provided. The parent company is called Amber Ledge Partners and we are presenting a new and very exciting eCommerce site called BrightHarborTrade.example.

Target Market(s)

Our target markets are in the Activities, Food and Beverage, Health and Beauty

Industry/Entity Type

Marketing

Contact Information for Business Card

We have 4 members that need cards...I will provide all info to the winner of the design contest
Business Address is
4870 West 63rd Avenue, Suite C207
Phoenix AZ 85731

Font styles to use
Serif
Sans Serif

Colors

Designer to choose colors to be used in the design.

Requirements
Must have
• The card must be memorable...should be unique in design but must exude integrity and be playful .
• I have provided several colors or our parent company...please feel free to use which ever
Nice to have
• I will leave this up to you. Feel free to use other images of your choosing that wraps around our client.....Activities, Dining, Health, Beauty
Should not have
• just dont be boring

```html
<!DOCTYPE html>
<html lang="en">
<head>
<meta charset="utf-8">
<title>BrightHarborTrade.example business card</title>
<link rel="stylesheet" href="https://fonts.googleapis.com/css2?family=Jost:wght@400;500;700&display=swap">
<style>
  :root {
    --backdrop: #2b2b2b;
    --card-white: #f6f6f6;
    --brand-blue: #2b7bb0;
    --brand-sky: #41bad8;
    --brand-green: #7cc23a;
    --brand-lime: #a8cc48;
    --text-grey: #4a4a4a;
  }
  * { margin: 0; padding: 0; box-sizing: border-box; }
  html, body {
    width: 1200px; height: 960px; overflow: hidden;
    background: var(--backdrop);
    font-family: "Jost", sans-serif;
  }
  .card {
    position: absolute;
    width: 600px; height: 342px;
    border-radius: 22px;
    overflow: hidden;
  }
  .card-front { left: 302px; top: 131px; background: var(--card-white); }
  .card-back {
    left: 299px; top: 490px;
    background: linear-gradient(135deg, var(--brand-sky) 0%, var(--brand-blue) 45%, var(--brand-blue) 100%);
  }
  .brand-wave { position: absolute; left: 0; top: 0; }
  .contact-block { position: absolute; left: 108px; top: 40px; }
  .person-name {
    font-size: 24px; font-weight: 500; color: var(--brand-blue);
    letter-spacing: 0.3px; line-height: 1.1;
  }
  .person-role {
    font-size: 15px; color: var(--brand-green); margin-top: 4px;
  }
  .address {
    font-size: 14.5px; color: var(--text-grey); line-height: 18px;
    margin-top: 8px; font-style: normal;
  }
  .contact-list { list-style: none; margin-top: 10px; }
  .contact-list li {
    display: flex; align-items: center; gap: 8px;
    font-size: 14px; color: var(--text-grey); line-height: 19.5px;
  }
  .contact-list svg { width: 13px; height: 13px; fill: var(--brand-blue); flex: none; }
  .site-brand { position: absolute; left: 108px; top: 244px; }
  .site-name {
    font-size: 21px; font-weight: 500; color: var(--brand-green); line-height: 1;
  }
  .site-tagline {
    font-size: 12px; color: var(--text-grey); letter-spacing: 0.9px; margin-top: 6px;
  }
  .brand-dot {
    position: absolute; left: 38px; top: 238px;
    width: 46px; height: 46px; border-radius: 50%;
    background: var(--brand-blue);
  }
  .parent-brand {
    position: absolute; left: 0; top: 0; width: 100%; height: 100%;
    display: flex; flex-direction: column; align-items: center;
  }
  .parent-dot {
    margin-top: 70px;
    width: 140px; height: 140px; border-radius: 50%;
    background: var(--brand-lime);
  }
  .parent-name {
    margin-top: 34px;
    font-size: 34px; font-weight: 700; color: var(--brand-lime);
  }
</style>
</head>
<body>

<section class="card card-front">
  <svg class="brand-wave" width="600" height="342" viewBox="0 0 600 342" role="img" aria-label="Large brand mark decoration in green and blue">
    <defs>
      <linearGradient id="waveTone" x1="0" y1="0" x2="1" y2="1">
        <stop offset="0" stop-color="#2b7bb0"/>
        <stop offset="0.55" stop-color="#7cc23a"/>
        <stop offset="1" stop-color="#7cc23a"/>
      </linearGradient>
    </defs>
    <path d="M455 342 C 420 250, 520 120, 555 0 L 600 0 L 600 342 Z" fill="url(#waveTone)"/>
  </svg>

  <div class="contact-block">
    <h1 class="person-name">DANIEL REYES</h1>
    <p class="person-role">CEO/FOUNDER</p>
    <address class="address">4870 West 63rd Avenue<br>Suite C207<br>Phoenix AZ 85731</address>
    <ul class="contact-list">
      <li><svg viewBox="0 0 24 24"><path d="M6.6 10.8a15 15 0 0 0 6.6 6.6l2.2-2.2c.3-.3.7-.4 1-.2 1.1.4 2.3.6 3.6.6.6 0 1 .4 1 1V20c0 .6-.4 1-1 1A17 17 0 0 1 3 4c0-.6.4-1 1-1h3.5c.6 0 1 .4 1 1 0 1.3.2 2.5.6 3.6.1.3 0 .7-.2 1z"/></svg>602 555 0148</li>
      <li><svg viewBox="0 0 24 24"><path d="M7 1h10a2 2 0 0 1 2 2v18a2 2 0 0 1-2 2H7a2 2 0 0 1-2-2V3a2 2 0 0 1 2-2zm0 3v14h10V4zm5 15.5a1.2 1.2 0 1 0 0 2.4 1.2 1.2 0 0 0 0-2.4z"/></svg>602 555 0193</li>
      <li><svg viewBox="0 0 24 24"><path d="M2 5h20v14H2zm2 2v.5l8 5 8-5V7zm0 2.8V17h16V9.8l-8 5z"/></svg>daniel@brightharbortrade.example</li>
      <li><svg viewBox="0 0 24 24"><path d="M12 2a10 10 0 1 0 0 20 10 10 0 0 0 0-20zm-1 17.9A8 8 0 0 1 4.1 11H7v2l3 3v3.9zm6.9-2.5A2 2 0 0 0 16 16h-1v-3H9v-2h2V9h2V7h2.5A8 8 0 0 1 17.9 17.4z"/></svg>www.brightharbortrade.example</li>
    </ul>
  </div>

  <span class="brand-dot"></span>
  <div class="site-brand">
    <p class="site-name">BrightHarborTrade.example</p>
    <p class="site-tagline">Activities-Dining-Health-Beauty</p>
  </div>
</section>

<section class="card card-back">
  <div class="parent-brand">
    <span class="parent-dot"></span>
    <p class="parent-name">Amber Ledge Partners</p>
  </div>
</section>

</body>
</html>
```